Online Shop - Website Design for up an coming art studio

We require a fully functional website design - not just design - but complete coded online shop website please, which should be a word press style frame work to allow ease up updating the site in the future. The website will sell art work from up and coming artists. The business is called "Brindle Harbor Studios". I have attached our logo to allow the submitted designs to tie in with this.

Industry/Entity Type

Shop

Coding

Coded - Design and coding required

Number of Pages Required

1 page

Colors

Designer to choose colors to be used in the design.

Requirements
Must have
• The website design must incorporate and fully functional online eCommerce shop feature.

```html
<!DOCTYPE html>
<html lang="en">
<head>
<meta charset="utf-8">
<title>Brindle Harbor Studios</title>
<link href="https://fonts.googleapis.com/css2?family=Montserrat:wght@500;600;700;800&family=Open+Sans:wght@400;600;700&display=swap" rel="stylesheet">
<style>
:root{
  --red:#e3173e;
  --ink:#2b2b2b;
  --body:#6a6a6a;
  --light:#f3f3f4;
  --white:#ffffff;
  --teal:#3fc6b8;
  --rainbow:linear-gradient(90deg,#f7941d,#ec1c5b 25%,#9b2fae 45%,#2d8fe0 62%,#3fc68a 80%,#f5d21a);
}
*{margin:0;padding:0;box-sizing:border-box}
html,body{width:1200px;height:3814px;overflow:hidden;background:var(--white)}
body{position:relative;font-family:'Open Sans',Arial,sans-serif;color:var(--body)}
.abs{position:absolute}
.heading{font-family:'Montserrat',Arial,sans-serif;font-weight:800;letter-spacing:.5px}
.grad-text{background:var(--rainbow);-webkit-background-clip:text;background-clip:text;color:transparent}
.btn{position:absolute;display:flex;align-items:center;justify-content:center;font-family:'Montserrat',Arial,sans-serif;font-weight:600;font-size:13px;border-radius:22px;text-transform:uppercase}
.btn-red{background:var(--red);color:var(--white)}
.btn-outline{border:2px solid var(--red);color:var(--red);background:var(--white)}

/* header */
.site-header{top:0;left:0;width:1200px;height:152px}
.brand{left:100px;top:20px;width:170px;display:flex;flex-direction:column;align-items:center}
.brand-mark{width:74px;height:74px;border-radius:50%;background:#3a3a3a}
.brand-name{margin-top:10px;font-family:'Montserrat',sans-serif;font-weight:700;font-size:17px;color:var(--ink);white-space:nowrap}
.main-nav{top:72px;font-family:'Montserrat',sans-serif;font-weight:600;font-size:13px;color:var(--ink)}
.main-nav.active{color:var(--red)}
.cart{left:1053px;top:62px;width:46px;height:46px;border-radius:50%;background:var(--red)}

/* hero */
.hero{top:148px;left:0}
.hero-title{left:94px;top:350px;font-size:50px;color:var(--white);font-family:'Montserrat',sans-serif;font-weight:700}
.hero-sub{left:94px;top:432px;font-size:19px;color:var(--white)}
.slider-dots{left:1143px;top:396px;display:flex;flex-direction:column;gap:7px}
.slider-dots span{width:11px;height:11px;border-radius:50%;border:2px solid var(--white)}
.slider-dots span.on{background:var(--red);border-color:var(--red)}

/* about */
.about-title{top:826px;left:0;width:1200px;text-align:center;font-size:44px}
.about-text{top:898px;left:190px;width:820px;text-align:center;font-size:13px;line-height:30px}
.about-art{left:885px;top:1050px;width:290px;height:150px;border-radius:60px 20px 20px 80px;background:linear-gradient(120deg,#f5d21a,#ec1c5b 40%,#9b2fae 65%,#2d8fe0)}

/* services */
.services-band{top:1207px;left:0;width:1200px;height:370px;background:linear-gradient(90deg,#f7941d,#ec1c5b 28%,#9b2fae 52%,#2d8fe0 70%,#3fc68a 86%,#f5d21a)}
.services-title{left:99px;top:1270px;font-size:40px;color:var(--white)}
.view-all{left:974px;top:1263px;width:124px;height:46px;background:rgba(255,255,255,.35);color:var(--white)}
.service-card{top:1373px;width:316px;height:297px;background:var(--white);box-shadow:0 4px 14px rgba(0,0,0,.08);padding:48px 20px 0}
.service-card.featured{background:var(--red)}
.service-card svg{display:block}
.service-name{margin-top:28px;font-family:'Montserrat',sans-serif;font-weight:700;font-size:15px;color:var(--red)}
.service-card.featured .service-name{color:#fde047}
.service-text{margin-top:14px;font-size:12px;line-height:22px}
.service-card.featured .service-text{color:var(--white)}
.card-go{position:absolute;left:50%;bottom:-22px;margin-left:-22px;width:44px;height:44px;border-radius:50%;background:var(--red);display:flex;align-items:center;justify-content:center;box-shadow:0 0 0 4px var(--white)}

/* testimonials */
.testimonials{top:1772px;left:0;width:1200px;height:452px;background:linear-gradient(135deg,#fafafa,#eeeef0 60%,#f7f7f8)}
.testi-title{left:120px;top:1838px;font-size:40px}
.testi-photo{left:158px;top:1958px;width:166px;height:166px;transform:rotate(45deg);border:6px solid var(--red);background:linear-gradient(135deg,#d8c7b8,#8a6d5b);}
.testi-quote{left:389px;top:1962px;width:700px;font-size:13px;line-height:27px;font-style:italic}
.testi-author{left:389px;top:2096px;font-family:'Montserrat',sans-serif;font-weight:700;font-size:14px;color:var(--red)}
.testi-arrows{left:1030px;top:2108px;color:#2d8fe0;font-size:20px;letter-spacing:16px}

/* products */
.products-title{left:112px;top:2318px;font-size:40px}
.prod-arrow{top:2326px;width:30px;height:30px;background:#eee;display:flex;align-items:center;justify-content:center;color:#777;font-size:16px}
.prod-img{width:404px;height:296px}
.prod-name{font-family:'Montserrat',sans-serif;font-weight:600;font-size:18px;line-height:30px;color:var(--ink);width:420px}
.prod-text{font-size:12px;line-height:22px;width:520px}
.prod-price{font-family:'Montserrat',sans-serif;font-weight:700;font-size:23px;color:var(--red)}
.prod-price s{color:#aaa;font-weight:500;margin-left:14px}

/* map */
.map-rule{left:0;width:1200px;height:3px;background:var(--rainbow)}
.map{top:3168px;left:0;width:1200px;height:367px;background:linear-gradient(160deg,#ececea,#e2e4e0 50%,#eaeae6)}
.address-card{left:457px;top:3292px;width:295px;height:132px;background:var(--white);box-shadow:0 3px 10px rgba(0,0,0,.12);text-align:center;padding-top:16px}
.address-card p{margin-top:8px;color:var(--red);font-size:13px;line-height:24px;padding:0 18px}

/* footer */
.social{top:3608px;width:44px;height:44px;border-radius:50%}
.footer-rule{left:452px;top:3690px;width:295px;height:2px;background:var(--teal)}
.copyright{top:3728px;left:0;width:1200px;text-align:center;font-size:12px;color:#888}
</style>
</head>
<body>

<header class="abs site-header">
  <div class="abs brand"><div class="brand-mark"></div><div class="brand-name">BRINDLE HARBOR</div></div>
  <span class="abs main-nav active" style="left:524px">HOME</span>
  <span class="abs main-nav" style="left:598px">ABOUT US</span>
  <span class="abs main-nav" style="left:693px">SERVICES</span>
  <span class="abs main-nav" style="left:785px">PROJECTS</span>
  <span class="abs main-nav" style="left:878px">BLOG</span>
  <span class="abs main-nav" style="left:948px">CONTACT US</span>
  <div class="abs cart">
    <svg width="46" height="46" viewBox="0 0 46 46"><path d="M15 17h3l3 11h9l2-8H19" fill="none" stroke="#fff" stroke-width="2"/><circle cx="22" cy="31" r="1.6" fill="#fff"/><circle cx="29" cy="31" r="1.6" fill="#fff"/></svg>
  </div>
</header>

<svg class="abs hero" width="1200" height="600" viewBox="0 0 1200 600" role="img" aria-label="Hero photograph of a smiling artist in a paint-splattered apron holding brushes in a colourful studio">
  <defs>
    <linearGradient id="heroFill" x1="0" x2="1" y1="0" y2="0">
      <stop offset="0" stop-color="#3a6fb0"/>
      <stop offset=".35" stop-color="#5a9bd1"/>
      <stop offset=".55" stop-color="#c9a48a"/>
      <stop offset=".75" stop-color="#d8473f"/>
      <stop offset="1" stop-color="#d9c7b0"/>
    </linearGradient>
    <linearGradient id="heroLine" x1="0" x2="1"><stop offset="0" stop-color="#f7941d"/><stop offset=".3" stop-color="#ec1c5b"/><stop offset=".55" stop-color="#9b2fae"/><stop offset=".75" stop-color="#2d8fe0"/><stop offset="1" stop-color="#3fc68a"/></linearGradient>
  </defs>
  <path d="M0 14 Q600 -4 1200 14 V520 Q600 640 0 520 Z" fill="url(#heroFill)"/>
  <path d="M0 14 Q600 -4 1200 14" fill="none" stroke="url(#heroLine)" stroke-width="3"/>
</svg>
<div class="abs hero-title">BRINDLE HARBOR STUDIOS</div>
<div class="abs hero-sub">We will sell artwork from upcoming artists</div>
<div class="btn btn-red" style="left:94px;top:499px;width:127px;height:44px">Shop Now</div>
<div class="abs slider-dots"><span class="on"></span><span></span><span></span><span></span><span></span></div>

<h1 class="abs heading grad-text about-title">ABOUT BRINDLE HARBOR STUDIOS</h1>
<p class="abs about-text">Sed ut perspiciatis unde omnis iste natus error sit voluptatem accusantium doloremque laudantium, totam rem aperiam, eaque ipsa quae ab illo inventore veritatis et quasi architecto beatae vitae dicta sunt explicabo. Nemo enim ipsam voluptatem quia voluptas sit aspernatur aut odit aut fugit, sed quia consequuntur magni dolores eos qui ratione voluptatem sequi nesciunt. Neque porro quisquam est, qui dolorem ipsum quia dolor sit amet, consectetur, adipisci velit, sed quia non numquam eius modi tempora incidunt ut labore et dolore magnam aliquam quaerat voluptatem. Ut enim ad minima veniam, quis nostrum exercitationem...</p>
<div class="btn btn-red" style="left:468px;top:1080px;width:127px;height:44px">Read More</div>
<div class="btn btn-outline" style="left:607px;top:1080px;width:128px;height:44px">Shop Now</div>
<div class="abs about-art" role="img" aria-label="Illustration of a profile silhouette with flowing rainbow-coloured hair"></div>

<section class="abs services-band"></section>
<h2 class="abs heading services-title">OUR SERVICES</h2>
<div class="btn view-all">View All</div>

<div class="abs service-card featured" style="left:99px">
  <svg width="34" height="34" viewBox="0 0 34 34"><path d="M6 28 L20 14 M20 14 a7 7 0 1 0 0-.1" fill="none" stroke="#fde047" stroke-width="4" stroke-linecap="round"/></svg>
  <div class="service-name">INTERIOR DESIGN</div>
  <p class="service-text">Nemo enim ipsam voluptatem quia voluptas sit aspernatur aut odit aut fugit, sed quia consequuntur magni dolores eos qui ratione ut odit aut fugi voluptatem....</p>
  <div class="card-go"><svg width="14" height="14" viewBox="0 0 14 14"><path d="M2 3l4 4-4 4M7 3l4 4-4 4" fill="none" stroke="#fff" stroke-width="2"/></svg></div>
</div>
<div class="abs service-card" style="left:442px">
  <svg width="34" height="34" viewBox="0 0 34 34"><rect x="2" y="2" width="13" height="13" fill="#f5c518"/><rect x="19" y="2" width="13" height="13" fill="#f5c518"/><rect x="2" y="19" width="13" height="13" fill="#f5c518"/><rect x="19" y="19" width="13" height="13" fill="#f5c518"/></svg>
  <div class="service-name">FLOOR DESIGN</div>
  <p class="service-text">Nemo enim ipsam voluptatem quia voluptas sit aspernatur aut odit aut fugit, sed quia consequuntur magni dolores eos qui ratione ut odit aut fugit voluptatem....</p>
  <div class="card-go"><svg width="14" height="14" viewBox="0 0 14 14"><path d="M2 3l4 4-4 4M7 3l4 4-4 4" fill="none" stroke="#fff" stroke-width="2"/></svg></div>
</div>
<div class="abs service-card" style="left:783px">
  <svg width="34" height="34" viewBox="0 0 34 34"><path d="M3 17 L17 4 L31 17 H27 V31 H7 V17 Z" fill="#f5c518"/><rect x="14" y="21" width="6" height="10" fill="#fff"/></svg>
  <div class="service-name">EXTERIOR DESIGN</div>
  <p class="service-text">Nemo enim ipsam voluptatem quia voluptas sit aspernatur aut odit aut fugit, sed quia consequuntur magni dolores eos qui ratione ut odit aut fugit voluptatem....</p>
  <div class="card-go"><svg width="14" height="14" viewBox="0 0 14 14"><path d="M2 3l4 4-4 4M7 3l4 4-4 4" fill="none" stroke="#fff" stroke-width="2"/></svg></div>
</div>

<section class="abs testimonials"></section>
<h2 class="abs heading grad-text testi-title">TESTIMONIALS</h2>
<div class="abs testi-photo" role="img" aria-label="Portrait photograph of a client in an art studio"></div>
<p class="abs testi-quote">" Neque porro quisquam est, qui dolorem ipsum quia dolor sit amet, consectetur, adipisci velit, sed quia non numquam eius modi tempora incidunt ut labore et dolore magnam aliquam quaerat voluptatem. Consectetur adipiscing elit, sed lorem ipsum quia dolor sed do eiusmod tempor incididunt ut labore et dolore magna aliqua. Ut enim ad minim veniam..."</p>
<div class="abs testi-author">- QUASI ARCHITECTO</div>
<div class="abs testi-arrows">‹›</div>

<h2 class="abs heading grad-text products-title">OUR PRODUCTS</h2>
<div class="abs prod-arrow" style="left:1018px">‹</div>
<div class="abs prod-arrow" style="left:1058px">›</div>

<div class="abs prod-img" style="left:112px;top:2425px;background:linear-gradient(135deg,#8a2a8c,#a23aa0 50%,#6b1f6e)" role="img" aria-label="Photograph of a bundle of colourful paint brushes on a purple background"></div>
<div class="abs prod-name" style="left:557px;top:2436px">NON NUMQUAM EIUS MODI TEMPORA INCIDUNT UT LABORE</div>
<p class="abs prod-text" style="left:557px;top:2510px">Sed ut perspiciatis unde omnis iste natus error sit voluptatem accusantium doloremque laudantium, totam rem aperiam, eaque ipsa quae ab illo inventore veritatis et quasi architecto beatae vitae dicta sunt explicabo.</p>
<div class="abs prod-price" style="left:557px;top:2614px">$76.18<s>$86.18</s></div>
<div class="btn btn-red" style="left:557px;top:2668px;width:129px;height:44px">Shop Now</div>

<div class="abs prod-name" style="left:112px;top:2780px">DEN NUMQUAM EIUS MODI TEMPORA INCIDUNT UT LAGEE</div>
<p class="abs prod-text" style="left:112px;top:2852px">Sed ut perspiciatis unde omnis iste natus error sit voluptatem accusantium doloremque laudantium, totam rem aperiam, eaque ipsa quae ab illo inventore veritatis et quasi architecto beatae vitae dicta sunt explicabo.</p>
<div class="abs prod-price" style="left:112px;top:2953px">$26.18<s>$86.18</s></div>
<div class="btn btn-red" style="left:112px;top:3010px;width:129px;height:44px">Shop Now</div>
<div class="abs prod-img" style="left:684px;top:2771px;background:linear-gradient(135deg,#e9e6e2,#f0dfe3 50%,#d9c2b2)" role="img" aria-label="Photograph of hands arranging colour swatches and fabric on a design table"></div>

<div class="abs map-rule" style="top:3165px"></div>
<div class="abs map" role="img" aria-label="Street map showing the studio location"></div>
<div class="abs map-rule" style="top:3535px"></div>
<svg class="abs" style="left:763px;top:3290px" width="24" height="34" viewBox="0 0 24 34"><path d="M12 33 C4 20 1 15 1 11 a11 11 0 0 1 22 0 c0 4-3 9-11 22z" fill="#e3173e"/><circle cx="12" cy="11" r="4" fill="#fff"/></svg>
<div class="abs address-card">
  <svg width="20" height="28" viewBox="0 0 24 34"><path d="M12 33 C4 20 1 15 1 11 a11 11 0 0 1 22 0 c0 4-3 9-11 22z" fill="#e3173e"/><circle cx="12" cy="11" r="4" fill="#fff"/></svg>
  <p>24 Larchwood Lane, Kelmore, Ardshire, KL4 7QT</p>
</div>

<div class="abs social" style="left:476px;background:#f7941d"></div>
<div class="abs social" style="left:545px;background:#2fa9e0"></div>
<div class="abs social" style="left:614px;background:#e3173e"></div>
<div class="abs social" style="left:682px;background:#d83a2e"></div>
<div class="abs footer-rule"></div>
<p class="abs copyright">© copyright 2017 Brindle Harbor Studios. All Rights Reserved</p>

</body>
</html>
```